Fastest Work at home Solution for Small Businesses

We need a web page for a product called *BrightReed*
We develop an innovative VPN Appliance (Model-Name ->Reed Alpha) that gives small business the possibility literally setup the possibility for Companies to let their employees work from home.
With our secure appliance we create safe connection between any business and the employee *working at home*
Our Products *Reed Alpha* are rolled out in minutes.
A. Employees can connect directly
B. Work from any location
C. All this without having to change the company firewall
Use case
=======
1. Go to our page
2. Select Product
3. Order
4. Connect to any Switch in the company
5. install software on employees laptop
***** INSTANT Connection ******
Target Market(s)
Businesses
Coding
Coded - Design and coding required
Number of Pages Required
3 page
Font styles to use
Look and feel
Each slider illustrates characteristics of the customer's brand and the style your logo design should communicate.

```html
<!DOCTYPE html>
<html lang="en">
<head>
<meta charset="utf-8">
<title>BrightReed – Fastest Work at home Solution for Small Businesses</title>
<link href="https://fonts.googleapis.com/css2?family=Lato:ital,wght@0,400;0,700;0,900;1,700&display=swap" rel="stylesheet">
<style>
:root{
  --navy:#1a32a3;
  --ink:#1b1c2c;
  --body:#2c2c34;
  --cyan:#45bdf0;
  --sky-light:#e4f4fd;
  --grey-bg:#f1f1f1;
  --card-shadow:rgba(0,0,0,.12);
  --footer:#232323;
  --white:#ffffff;
}
*{box-sizing:border-box;margin:0;padding:0}
html,body{width:1200px;height:4187px;overflow:hidden}
body{position:relative;font-family:'Lato',sans-serif;color:var(--body);background:var(--white)}
.abs{position:absolute}

/* header */
.brand{display:flex;align-items:center;gap:12px;font-weight:900;font-size:38px;color:var(--ink)}
.brand-mark{width:30px;height:30px;background:var(--navy);border-radius:4px}
.site-header .brand{left:75px;top:38px}
.signup{left:955px;top:37px;width:124px;height:46px;border-radius:23px;background:var(--cyan);color:var(--white);font-weight:700;font-size:18px;display:flex;align-items:center;justify-content:center}
.menu-icon{left:1106px;top:50px;width:20px}

/* hero */
.hero-bg{left:325px;top:0;width:875px;height:770px;background:linear-gradient(180deg,#f3fafe 0%,var(--sky-light) 100%);border-bottom-left-radius:70px;clip-path:polygon(0 0,100% 0,100% 100%,6% 100%,0 0)}
.hero-art{left:540px;top:145px;width:630px;height:570px;border-radius:40px;background:linear-gradient(160deg,#c9d4f3 0%,#d8dde8 60%,#e9ecf4 100%)}
.hero-pattern{left:18px;top:455px;width:300px;height:300px;border-radius:30px;background:linear-gradient(135deg,#c3cdee 0%,#ccf0fb 100%);opacity:.7}
.hero-title{left:75px;top:244px;font-size:50px;font-weight:900;line-height:65px;color:var(--navy)}
.hero-title span{background:var(--white);padding:0 8px 0 0;display:inline-block}
.btn{background:var(--cyan);color:var(--white);font-weight:700;font-size:22px;border-radius:31px;display:flex;align-items:center;justify-content:center}
.hero .btn{left:75px;top:474px;width:205px;height:60px}

/* products */
.section-title{font-size:44px;font-weight:900;color:var(--ink)}
.products-head{left:0;top:836px;width:1200px;text-align:center}
.products-sub{font-size:28px;font-weight:700;color:var(--ink);margin-top:12px}
.products-sub em{font-style:normal;color:var(--navy)}
.feature h3{font-size:36px;font-weight:700;color:var(--navy);line-height:42px}
.feature p{font-size:15.5px;line-height:32px;color:var(--body);margin-top:24px;width:500px}
.feature a{display:block;margin-top:24px;font-size:18px;color:var(--cyan);text-decoration:underline}
.art{border-radius:30px}
.art-1{left:38px;top:1025px;width:572px;height:275px;background:linear-gradient(180deg,#e6e6f1,#c9cbe0)}
.art-2{left:625px;top:1395px;width:490px;height:365px;background:linear-gradient(180deg,#ececec,#cfd2e6)}
.art-3{left:85px;top:1805px;width:480px;height:340px;border-radius:120px 90px 140px 80px;background:linear-gradient(160deg,#e2e6f6,#d3d9f1)}
.feature-1{left:614px;top:1035px}
.feature-2{left:75px;top:1432px}
.feature-3{left:614px;top:1830px}

/* use case */
.grey-shape{left:0;width:1200px}
.usecase-title{left:75px;top:2332px}
.usecase-desc{left:75px;top:2410px;width:660px;font-size:17px;line-height:31px;color:var(--body)}
.arrows{display:flex;gap:18px}
.arrows svg{width:24px;height:36px}
.uc-arrows{left:1060px;top:2377px}
.cards{left:75px;top:2504px;display:flex;gap:28px}
.uc-card{position:relative;width:241px;height:247px;background:var(--white);box-shadow:0 2px 10px var(--card-shadow);text-align:center;padding:28px 22px 0;overflow:hidden}
.uc-card svg{width:50px;height:60px}
.uc-card h4{font-size:20px;font-weight:700;color:var(--navy);margin-top:12px;line-height:24px;position:relative;z-index:1}
.uc-card p{font-size:16px;line-height:27px;color:#444;margin-top:10px;position:relative;z-index:1}
.uc-num{position:absolute;right:10px;bottom:-14px;font-size:110px;font-weight:700;font-style:italic;color:#e8e8e8;line-height:1}

/* cta */
.cta{left:0;top:2832px;width:1200px;height:400px;background:linear-gradient(90deg,#3fb6ec 0%,#1f5fcf 55%,#0b2ba6 100%)}
.cta-pattern{position:absolute;border-radius:30px;background:rgba(255,255,255,.12)}
.cta h2{position:absolute;left:0;top:66px;width:1200px;text-align:center;font-size:43px;font-weight:900;line-height:52px;color:var(--white)}
.cta .btn{position:absolute;left:498px;top:262px;width:204px;height:61px}

/* testimonials */
.t-title{left:75px;top:3365px}
.t-arrows{left:1060px;top:3378px}
.quotes{left:75px;top:3455px;display:flex;gap:28px}
.quote-card{position:relative;width:512px;height:314px;background:var(--white);box-shadow:0 2px 10px var(--card-shadow);padding:32px 30px 0}
.quote-mark{position:absolute;font-size:130px;font-weight:900;color:#e2e2e2;line-height:1;font-family:Georgia,serif}
.quote-open{left:16px;top:4px}
.quote-close{right:14px;bottom:-38px}
.quote-card p{position:relative;font-size:15.5px;line-height:32.5px;color:var(--body)}
.quote-card h5{position:relative;font-size:19px;font-weight:700;color:var(--navy);margin-top:12px}
.quote-card small{position:relative;font-size:13px;color:var(--body)}

/* footer */
.site-footer{left:0;top:3842px;width:1200px;height:345px;background:var(--footer);color:var(--white)}
.site-footer .brand{position:absolute;left:75px;top:88px;color:var(--white);font-size:44px}
.site-footer .brand-mark{background:var(--white)}
.copyright{position:absolute;left:75px;top:160px;font-size:14px;line-height:25px}
.socials{position:absolute;left:75px;top:218px;display:flex;gap:30px}
.socials span{width:22px;height:22px;border-radius:50%;background:var(--white)}
.footer-col{position:absolute;top:68px}
.footer-col h6{font-size:21px;font-weight:700}
.footer-col li{list-style:none;font-size:13.5px;line-height:33px}
.footer-col ul{margin-top:4px}
</style>
</head>
<body>

<header class="site-header">
  <div class="brand abs"><span class="brand-mark"></span>BrightReed</div>
  <div class="signup abs">Sign Up</div>
  <svg class="menu-icon abs" viewBox="0 0 20 20" aria-hidden="true"><rect y="1" width="20" height="3" fill="#1a32a3"/><rect y="8.5" width="20" height="3" fill="#1a32a3"/><rect y="16" width="20" height="3" fill="#1a32a3"/></svg>
</header>

<section class="hero">
  <div class="hero-bg abs"></div>
  <div class="hero-art abs" role="img" aria-label="Illustration of a woman working on a laptop at a desk, with a network of connected boxes above"></div>
  <div class="hero-pattern abs" role="img" aria-label="Decorative network of connected dots"></div>
  <h1 class="hero-title abs"><span>Fastest Work at home</span><br><span>Solution for</span><br><span>Small Businesses</span></h1>
  <a class="btn abs">Try it Now</a>
</section>

<section class="products">
  <div class="products-head abs">
    <h2 class="section-title">Our Products</h2>
    <p class="products-sub"><em>Reed Alpha</em> are rolled out in minutes</p>
  </div>

  <div class="art art-1 abs" role="img" aria-label="Illustration of two employees working on laptops"></div>
  <div class="feature feature-1 abs">
    <h3>Employees<br>can connect directly</h3>
    <p>Sed ut perspiciatis unde omnis iste natus error sit voluptatem accusantium doloremque laudantium, totam rem aperiam, eaque ipsa quae ab illo inventore veritatis et quasi architecto beatae vitae dicta sunt explicabo.</p>
    <a>Learn More</a>
  </div>

  <div class="feature feature-2 abs">
    <h3>Work from any<br>location</h3>
    <p>Sed ut perspiciatis unde omnis iste natus error sit voluptatem accusantium doloremque laudantium, totam rem aperiam, eaque ipsa quae ab illo inventore veritatis et quasi architecto beatae vitae dicta sunt explicabo.</p>
    <a>Learn More</a>
  </div>
  <div class="art art-2 abs" role="img" aria-label="Illustration of a person lying on the floor working on a laptop beside shelves"></div>

  <div class="art art-3 abs" role="img" aria-label="Illustration of a person sitting with a laptop next to an upload progress bar"></div>
  <div class="feature feature-3 abs">
    <h3>All this without having to<br>change the company firewall</h3>
    <p>Sed ut perspiciatis unde omnis iste natus error sit voluptatem accusantium doloremque laudantium, totam rem aperiam, eaque ipsa quae ab illo inventore veritatis et quasi architecto beatae vitae dicta sunt explicabo.</p>
    <a>Learn More</a>
  </div>
</section>

<section class="use-case">
  <svg class="grey-shape abs" style="top:2265px;height:567px" viewBox="0 0 1200 567" preserveAspectRatio="none" aria-hidden="true"><path d="M0 0 H700 Q766 0 766 66 L690 567 H0 Z" fill="#f1f1f1"/></svg>
  <h2 class="section-title usecase-title abs">Use Case</h2>
  <p class="usecase-desc abs">Sed ut perspiciatis unde omnis iste natus error sit voluptatem accusantium doloremque laudantium,</p>
  <div class="arrows uc-arrows abs">
    <svg viewBox="0 0 24 36" aria-hidden="true"><path d="M18 4 L6 18 L18 32" stroke="#1b1c2c" stroke-width="5" fill="none"/></svg>
    <svg viewBox="0 0 24 36" aria-hidden="true"><path d="M6 4 L18 18 L6 32" stroke="#1b1c2c" stroke-width="5" fill="none"/></svg>
  </div>
  <div class="cards abs">
    <div class="uc-card">
      <svg viewBox="0 0 50 60" aria-hidden="true"><path d="M4 2 H32 L46 16 V58 H4 Z" fill="#45bdf0"/><path d="M32 2 V16 H46" fill="#9edcf7"/><rect x="13" y="30" width="24" height="3" fill="#fff"/><rect x="13" y="38" width="24" height="3" fill="#fff"/><rect x="13" y="46" width="24" height="3" fill="#fff"/></svg>
      <h4>Go to our page</h4>
      <p>Sed ut perspiciatis unde omnis iste natus error sit voluptatem.</p>
      <span class="uc-num">1</span>
    </div>
    <div class="uc-card">
      <svg viewBox="0 0 50 60" aria-hidden="true"><rect x="4" y="6" width="42" height="52" rx="5" fill="#45bdf0"/><rect x="17" y="1" width="16" height="10" rx="3" fill="#45bdf0" stroke="#fff" stroke-width="2"/><g fill="#fff"><circle cx="14" cy="24" r="2.5"/><circle cx="14" cy="34" r="2.5"/><circle cx="14" cy="44" r="2.5"/><rect x="20" y="22.5" width="18" height="3"/><rect x="20" y="32.5" width="18" height="3"/><rect x="20" y="42.5" width="18" height="3"/></g></svg>
      <h4>Select Product</h4>
      <p>Sed ut perspiciatis unde omnis iste natus error sit voluptatem.</p>
      <span class="uc-num">2</span>
    </div>
    <div class="uc-card">
      <svg viewBox="0 0 60 60" aria-hidden="true"><path d="M2 8 H12 L18 40 H52 L58 16 H15" fill="none" stroke="#45bdf0" stroke-width="5"/><path d="M15 16 H58 L52 40 H19 Z" fill="#45bdf0"/><circle cx="22" cy="52" r="5" fill="#45bdf0"/><circle cx="48" cy="52" r="5" fill="#45bdf0"/></svg>
      <h4>Order</h4>
      <p>Sed ut perspiciatis unde omnis iste natus error sit voluptatem.</p>
      <span class="uc-num">3</span>
    </div>
    <div class="uc-card">
      <svg viewBox="0 0 60 60" aria-hidden="true"><path d="M10 26 A20 20 0 0 1 46 16" fill="none" stroke="#45bdf0" stroke-width="7"/><path d="M52 6 V24 H34 Z" fill="#45bdf0"/><path d="M50 34 A20 20 0 0 1 14 44" fill="none" stroke="#45bdf0" stroke-width="7"/><path d="M8 54 V36 H26 Z" fill="#45bdf0"/></svg>
      <h4>Connect to any Switch in the company</h4>
      <p>Sed ut perspiciatis unde omnis iste natus error sit voluptatem.</p>
      <span class="uc-num">4</span>
    </div>
  </div>
</section>

<section class="cta abs">
  <div class="cta-pattern" style="left:18px;top:0;width:200px;height:240px" role="img" aria-label="Decorative network of connected dots"></div>
  <div class="cta-pattern" style="left:850px;top:150px;width:340px;height:250px;background:rgba(10,30,140,.25)" role="img" aria-label="Decorative network of connected dots"></div>
  <h2>Our secure appliance we create safe connection<br>between any business and the employee<br>Working at Home</h2>
  <a class="btn">Try it Now</a>
</section>

<section class="testimonials">
  <svg class="grey-shape abs" style="top:3298px;height:544px" viewBox="0 0 1200 544" preserveAspectRatio="none" aria-hidden="true"><path d="M0 0 H700 Q766 0 766 66 L690 544 H0 Z" fill="#f1f1f1"/></svg>
  <h2 class="section-title t-title abs">What Our Client Says</h2>
  <div class="arrows t-arrows abs">
    <svg viewBox="0 0 24 36" aria-hidden="true"><path d="M18 4 L6 18 L18 32" stroke="#1b1c2c" stroke-width="5" fill="none"/></svg>
    <svg viewBox="0 0 24 36" aria-hidden="true"><path d="M6 4 L18 18 L6 32" stroke="#1b1c2c" stroke-width="5" fill="none"/></svg>
  </div>
  <div class="quotes abs">
    <div class="quote-card">
      <span class="quote-mark quote-open">“</span>
      <p>Sed ut perspiciatis unde omnis iste natus error sit voluptatem accusantium doloremque laudantium, totam rem aperiam, eaque ipsa quae ab illo inventore veritatis et quasi architecto beatae vitae dicta sunt explicabo&nbsp; sed quia consequuntur magni dolores eos qui ratione voluptatem sequi nesciunt..”</p>
      <h5>Name Heading</h5>
      <small>Company Name</small>
      <span class="quote-mark quote-close">”</span>
    </div>
    <div class="quote-card">
      <span class="quote-mark quote-open">“</span>
      <p>Sed ut perspiciatis unde omnis iste natus error sit voluptatem accusantium doloremque laudantium, totam rem aperiam, eaque ipsa quae ab illo inventore veritatis et quasi architecto beatae vitae dicta sunt explicabo&nbsp; sed quia consequuntur magni dolores eos qui ratione voluptatem sequi nesciunt..”</p>
      <h5>Name Heading</h5>
      <small>Company Name</small>
      <span class="quote-mark quote-close">”</span>
    </div>
  </div>
</section>

<footer class="site-footer abs">
  <div class="brand"><span class="brand-mark"></span>BrightReed</div>
  <p class="copyright">Copyright © 2021 Company Name.<br>All Right reserved</p>
  <div class="socials" aria-label="Social links"><span></span><span></span><span></span><span></span><span></span></div>
  <div class="footer-col" style="left:433px">
    <h6>Company</h6>
    <ul><li>Sed ut perspiciatis</li><li>Unde omnis iste</li><li>Natus error sit voluptatem</li><li>Accusantium</li><li>Doloremque</li></ul>
  </div>
  <div class="footer-col" style="left:685px">
    <h6>Resources</h6>
    <ul><li>Sed ut perspiciatis</li><li>Unde omnis iste</li><li>Natus error sit voluptatem</li><li>Accusantium</li><li>Doloremque</li></ul>
  </div>
  <div class="footer-col" style="left:934px">
    <h6>Support</h6>
    <ul><li>Sed ut perspiciatis</li><li>Unde omnis iste</li><li>Natus error sit voluptatem</li><li>Accusantium</li><li>Doloremque</li></ul>
  </div>
</footer>

</body>
</html>
```